Corvane Business Cards

Front of business card will have logo, name, address, & telephone number. Back of card will have a list of services provided - Roads, Substation Pads, Temporary Pads, Site Pads, Land Leveling, Powerline Row Cleaning, Land Clearing, Gates, Fencing, Construction Entrances, Excavation, Trenching, Underground Utilities, Directional Boring, Pile Driving. We are a construction company that uses heavy equipment like bulldozers, motor graders/blades, dump trucks, backhoes, hydro axes, & skid loaders. We build roads, pads, & install electric utility lines & waterlines underground. This logo is new. The word "Construction" can be smaller as uploaded 2 example edited logos. We will be using this card design for many employees.
Target Market(s)
Industrial Electric Powerline, Wind Turbine, Solar Panel, & Water Utility companies.
Contact Information for Business Card
Name/Position - Dwayne Halster - Owner
Address: 4875 FM 309
Alder Falls, NM 87412
Phone number - (555) 482-5096

```html
<!DOCTYPE html>
<html lang="en">
<head>
<meta charset="utf-8">
<title>Corvane Construction Business Cards</title>
<link rel="stylesheet" href="https://fonts.googleapis.com/css2?family=Josefin+Sans:wght@300;400;600&display=swap">
<style>
  :root {
    --maroon: #35121a;
    --card-white: #f0f0f0;
    --backdrop: #e4e4e4;
    --muted: #7b7b7b;
    --rule: #8a8a8a;
    --light-text: #ece6e6;
  }
  * { box-sizing: border-box; margin: 0; padding: 0; }
  html, body {
    width: 1200px; height: 1200px; overflow: hidden;
    background: var(--backdrop);
    font-family: "Josefin Sans", sans-serif;
  }
  .canvas { position: relative; width: 1200px; height: 1200px; }
  .card {
    position: absolute; left: 227px; width: 746px; height: 426px;
  }
  .card-front { top: 135px; background: var(--card-white); color: var(--maroon); }
  .card-back { top: 639px; background: var(--maroon); color: var(--light-text); }

  .wordmark {
    position: absolute; font-weight: 600; text-transform: uppercase;
    line-height: 1.05; letter-spacing: 1px;
  }
  .card-front .wordmark { left: 27px; top: 78px; font-size: 46px; }
  .card-back .wordmark { left: 0; right: 0; top: 72px; font-size: 46px; text-align: center; }

  .holder-name {
    position: absolute; left: 27px; top: 268px;
    font-size: 28px; font-weight: 600; letter-spacing: 1px; text-transform: uppercase;
  }
  .holder-role {
    position: absolute; left: 27px; top: 307px;
    font-size: 21px; font-weight: 300; color: var(--muted);
  }
  .divider {
    position: absolute; left: 100px; right: 0; top: 322px;
    height: 1px; background: var(--rule);
  }
  .phone {
    position: absolute; left: 27px; top: 364px;
    font-size: 21px; font-weight: 300; color: var(--muted);
  }
  .phone-label { color: var(--maroon); font-weight: 400; }
  .address {
    position: absolute; right: 27px; top: 336px;
    font-size: 21px; font-weight: 300; color: var(--muted);
    text-align: right; line-height: 29px;
  }

  .services {
    position: absolute; left: 30px; right: 27px; top: 270px;
    font-size: 20px; font-weight: 300; line-height: 29.5px;
    text-align: justify; text-align-last: justify;
  }
  .services span { display: block; text-align-last: justify; }
</style>
</head>
<body>
<main class="canvas">
  <section class="card card-front" aria-label="Business card front">
    <div class="wordmark">Corvane<br>Construction</div>
    <h1 class="holder-name">Dwayne Halster</h1>
    <p class="holder-role">Owner</p>
    <div class="divider"></div>
    <p class="phone"><span class="phone-label">P.</span> (555) 482-5096</p>
    <p class="address">4875 FM 309<br>Alder Falls, NM 87412</p>
  </section>

  <section class="card card-back" aria-label="Business card back">
    <div class="wordmark">Corvane<br>Construction</div>
    <p class="services">
      <span>• &nbsp;Roads &nbsp;• &nbsp;Substation Pads &nbsp;• &nbsp;Temporary Pads &nbsp;• &nbsp;Site Pads</span>
      <span>• Land Leveling • Powerline Row Cleaning • Land Clearing • Gates</span>
      <span>• &nbsp;Fencing &nbsp;• &nbsp;Construction Entrances &nbsp;• &nbsp;Excavation &nbsp;• &nbsp;Trenching</span>
      <span>• &nbsp;Underground Utilities &nbsp;• &nbsp;Directional Boring &nbsp;• &nbsp;Pile Driving.</span>
    </p>
  </section>
</main>
</body>
</html>
```